Verlindo Magician

I want the business card for my business to give to people who watch that later I will be employed to show magic here is my website http://www.balsamomagicien.com/I want the interesting design , i am very opened for formal and informal, I watch a lot of design so don't stick to the common shape and form but i hope it can also be produced the thing to write on will be the same as in picture that i will upload , i also will upload the logo for you that so can be easy to useDenis CostilleMagicianMAGICIAN VERLINDO 17 rue des Tilleuls - 25000 BESANÇON contact@verlindoillusions.example tel. 0381 946 157 tel. 0674 219 503

```html
<!DOCTYPE html>
<html lang="fr">
<head>
<meta charset="utf-8">
<title>Verlindo Magician – Business Card</title>
<link rel="stylesheet" href="https://fonts.googleapis.com/css2?family=Jost:wght@300;400&display=swap">
<style>
  :root {
    --backdrop: #e4e4e4;
    --ink: #0b0b0b;
    --paper: #ffffff;
    --accent: #e8222a;
    --card-w: 800px;
    --card-h: 456px;
  }
  * { margin: 0; padding: 0; box-sizing: border-box; }
  html, body {
    width: 1125px; height: 1200px; overflow: hidden;
    background: var(--backdrop);
    font-family: "Jost", "Futura", sans-serif;
  }
  .canvas { position: relative; width: 1125px; height: 1200px; }
  .card {
    position: absolute; left: 166px;
    width: var(--card-w); height: var(--card-h);
    overflow: hidden;
    box-shadow: 0 3px 8px rgba(0,0,0,.25);
  }
  .card--front { top: 103px; background: var(--paper); }
  .card--back { top: 620px; background: var(--accent); }

  .front-swoosh { position: absolute; inset: 0; width: 100%; height: 100%; }

  .contact-block { position: absolute; left: 40px; top: 193px; color: var(--paper); }
  .contact-block__name { color: var(--accent); font-size: 29px; font-weight: 400; line-height: 1; }
  .contact-block__role { font-size: 20px; font-weight: 400; margin-top: 8px; }
  .contact-block__address { font-size: 19px; font-weight: 400; line-height: 25px; margin-top: 14px; margin-left: 2px; }
  .contact-list { list-style: none; margin-top: 10px; margin-left: 2px; }
  .contact-list__item { display: flex; align-items: center; gap: 10px; font-size: 19px; line-height: 26px; }
  .contact-list__item--small { font-size: 18px; }
  .contact-list__icon { width: 18px; height: 18px; flex: none; fill: var(--accent); }

  .portrait {
    position: absolute;
    border-radius: 46% 46% 8px 8px;
  }
  .portrait--front {
    left: 556px; top: 40px; width: 170px; height: 186px;
    background: linear-gradient(180deg, #2a2a2a 0%, #0b0b0b 100%);
  }
  .portrait--back {
    left: 306px; top: 76px; width: 222px; height: 280px;
    background: linear-gradient(180deg, #1a1a1a 0%, #0b0b0b 100%);
  }

  .brand-name {
    position: absolute; left: 520px; top: 248px; width: 240px;
    text-align: center; color: var(--ink);
    font-size: 34px; font-weight: 300; letter-spacing: 1px;
  }

  .back-url {
    position: absolute; left: 0; right: 0; top: 396px;
    text-align: center; color: var(--paper);
    font-size: 19px; font-weight: 400; letter-spacing: 2.5px;
  }
</style>
</head>
<body>
<main class="canvas">

  <section class="card card--front">
    <svg class="front-swoosh" viewBox="0 0 800 456" preserveAspectRatio="none" aria-hidden="true">
      <path fill="#0b0b0b" d="M0,0 H334 C345,200 520,380 657,456 H0 Z"/>
      <path fill="#ffffff" d="M294,28 C322,220 470,380 603,456 L618,456 C484,372 340,212 300,28 Z"/>
    </svg>

    <div class="contact-block">
      <h1 class="contact-block__name">Marc Ravoulet</h1>
      <p class="contact-block__role">Magician</p>
      <p class="contact-block__address">MAGICIAN VERLINDO<br>17 rue des Tilleuls - 25000 BESANÇON</p>
      <ul class="contact-list">
        <li class="contact-list__item">
          <svg class="contact-list__icon" viewBox="0 0 24 24"><path d="M6.6 10.8a15 15 0 0 0 6.6 6.6l2.2-2.2c.3-.3.7-.4 1-.2 1.1.4 2.3.6 3.6.6.6 0 1 .4 1 1V20c0 .6-.4 1-1 1A17 17 0 0 1 3 4c0-.6.4-1 1-1h3.5c.6 0 1 .4 1 1 0 1.3.2 2.5.6 3.6.1.3 0 .7-.2 1z"/></svg>
          0381 946 157
        </li>
        <li class="contact-list__item">
          <svg class="contact-list__icon" viewBox="0 0 24 24"><path d="M6.6 10.8a15 15 0 0 0 6.6 6.6l2.2-2.2c.3-.3.7-.4 1-.2 1.1.4 2.3.6 3.6.6.6 0 1 .4 1 1V20c0 .6-.4 1-1 1A17 17 0 0 1 3 4c0-.6.4-1 1-1h3.5c.6 0 1 .4 1 1 0 1.3.2 2.5.6 3.6.1.3 0 .7-.2 1z"/></svg>
          0674 219 503
        </li>
        <li class="contact-list__item contact-list__item--small">
          <svg class="contact-list__icon" viewBox="0 0 24 24"><path d="M3 6h18v12H3z M3 6l9 7 9-7" fill="none" stroke="#e8222a" stroke-width="0"/><path d="M3 6h18l-9 7z M3 8l9 7 9-7v10H3z"/></svg>
          contact@verlindoillusions.example
        </li>
        <li class="contact-list__item contact-list__item--small">
          <svg class="contact-list__icon" viewBox="0 0 24 24"><circle cx="12" cy="12" r="10"/><path fill="#0b0b0b" d="M7 7c2 0 3 1 3 3s-2 2-2 4-2 1-3 0c-1-2 0-7 2-7zm8 2c2 0 3 2 2 4s-2 3-3 5c-1 1-2 0-2-1s1-2 0-4 1-4 3-4z"/></svg>
          www.verlindoillusions.example
        </li>
      </ul>
    </div>

    <div class="portrait portrait--front" role="img" aria-label="Illustration of the magician holding a playing card"></div>
    <p class="brand-name">VERLINDO</p>
  </section>

  <section class="card card--back">
    <div class="portrait portrait--back" role="img" aria-label="Illustration of the magician holding a playing card"></div>
    <p class="back-url">www.verlindoillusions.example</p>
  </section>

</main>
</body>
</html>
```